Moderne Visitenkarten für Medizintechnikfirma
Zielgruppe
Vertriebsfirma von moderner und innovativer Medizintechnik
Zielgruppe: Ärzte, Kliniken, Medizintechnikfirmen, Patienten
Aufgabenstellung
Besonderes, modernes, auffälliges und ansprechendes Design ohne überladen oder aufdringlich zu sein
Farbenorientierung kann am Logo und der Website geschehen. Wenn zum Logo harmonierend, sind aber auch andere Farben gerne gesehen.
Format: eher horizontal, vertikal aber auch möglich, abgerundete Ecken einplanen
Wenn möglich folgende Infos bitte schon auf die Karten bringen (pro Person eine Karte):
Konrad Faltermann (CEO)
konrad.faltermann@vitalis-partner.de
(Vitalis Partner GmbH
Lindenhof 12
26210 Grünstedt)
www.vitalis-partner.de
info@vitalis-partner.de
Jonas Prasken (CoS)
jonas.prasken@vitalis-partner.de
Die allgemeinen Firmeninfos können deutlich kleiner sein. Anschrift nur wenn es dadurch nicht zu viel werden würde.

```html
<!DOCTYPE html>
<html lang="de">
<head>
<meta charset="utf-8">
<title>Vitalis Partner – Visitenkarten</title>
<link rel="stylesheet" href="https://fonts.googleapis.com/css2?family=Inter:wght@300;400&display=swap">
<style>
  :root {
    --purple: #52457f;
    --orange: #d0452b;
    --ink: #2b2b2b;
    --frame: #6a6a6a;
    --paper: #ffffff;
  }
  html, body { margin: 0; padding: 0; overflow: hidden; }
  body {
    width: 1200px; height: 773px; position: relative;
    background: var(--paper);
    font-family: "Inter", Arial, sans-serif;
    color: var(--ink);
  }
  .card {
    position: absolute; width: 510px; height: 329px;
    background: var(--paper);
    box-shadow: inset 0 0 0 1px var(--frame);
    overflow: hidden;
  }
  .card--front { left: 345px; top: 20px; }
  .card--konrad { left: 35px; top: 408px; }
  .card--jonas { left: 656px; top: 408px; }

  .band { position: absolute; left: 0; bottom: 0; width: 510px; height: 18px; display: block; }

  .brand { position: absolute; display: flex; align-items: center; color: var(--purple); font-weight: 400; white-space: nowrap; }
  .brand__dot { border-radius: 50%; background: var(--purple); flex: none; }
  .brand--large { left: 100px; top: 130px; font-size: 35px; letter-spacing: -0.3px; }
  .brand--large .brand__dot { width: 40px; height: 40px; margin-right: 22px; }
  .brand--small { left: 45px; top: 40px; font-size: 14px; }
  .brand--small .brand__dot { width: 30px; height: 30px; margin-right: 11px; }

  .person {
    position: absolute; left: 116px; top: 104px; margin: 0;
    font-size: 21px; font-weight: 400; color: var(--purple);
    font-variant: small-caps; letter-spacing: 0.2px; line-height: 1;
  }
  .person__role { font-size: 16px; font-variant: normal; }
  .direct { position: absolute; left: 116px; top: 135px; font-size: 16px; line-height: 20px; font-weight: 300; }
  .rule { position: absolute; left: 116px; right: 0; top: 202px; height: 1px; background: var(--purple); }
  .company { position: absolute; left: 116px; top: 224px; font-size: 14.5px; line-height: 18px; font-weight: 300; }
  .company__name { font-weight: 400; }
  .line { display: flex; align-items: center; white-space: nowrap; }
  .icon { width: 13px; height: 12px; margin-right: 5px; flex: none; }
  .sep { margin: 0 6px; }
</style>
</head>
<body>

<section class="card card--front" aria-label="Vorderseite">
  <div class="brand brand--large"><span class="brand__dot"></span>Vitalis Partner</div>
  <svg class="band" viewBox="0 0 510 18" aria-hidden="true">
    <polygon points="0,0 347,0 331,18 0,18" fill="var(--purple)"/>
    <polygon points="379,0 510,0 510,18 363,18" fill="var(--orange)"/>
  </svg>
</section>

<section class="card card--konrad" aria-label="Rückseite Konrad Faltermann">
  <div class="brand brand--small"><span class="brand__dot"></span>Vitalis Partner</div>
  <h2 class="person">Konrad Faltermann <span class="person__role">(CEO)</span></h2>
  <div class="direct">
    <div class="line"><svg class="icon" viewBox="0 0 13 12"><rect x="3" y="1" width="6" height="10" rx="1" fill="none" stroke="var(--purple)" stroke-width="1.3"/><path d="M10 3.5q1.5 2.5 0 5" fill="none" stroke="var(--purple)"/></svg>+49 170 42 56 93 07</div>
    <div class="line"><svg class="icon" viewBox="0 0 13 12"><rect x="0.5" y="2.5" width="12" height="8" fill="none" stroke="var(--purple)"/><path d="M0.5 2.5l6 5 6-5" fill="none" stroke="var(--purple)"/></svg>konrad.faltermann@vitalis-partner.de</div>
  </div>
  <div class="rule"></div>
  <div class="company">
    <div class="company__name">Vitalis Partner GmbH</div>
    <div>Lindenhof 12<span class="sep">·</span>D-26210 Grünstedt</div>
    <div class="line"><svg class="icon" viewBox="0 0 13 12"><path d="M1 5q5.5-5 11 0l-2 1.5-1.5-2h-4L3 6.5z" fill="var(--ink)"/><rect x="3" y="6.5" width="7" height="4" rx="1" fill="var(--ink)"/></svg>0800 5104 228<span class="sep">·</span><svg class="icon" viewBox="0 0 13 12"><rect x="0.5" y="2.5" width="12" height="8" fill="none" stroke="var(--purple)"/><path d="M0.5 2.5l6 5 6-5" fill="none" stroke="var(--purple)"/></svg>info@vitalis-partner.de</div>
    <div class="line"><svg class="icon" viewBox="0 0 13 12"><circle cx="6.5" cy="6" r="5.3" fill="none" stroke="var(--ink)"/><path d="M4 3l3 1-1 3 2 2" fill="none" stroke="var(--ink)" stroke-width="1.4"/></svg>www.vitalis-partner.de</div>
  </div>
  <svg class="band" viewBox="0 0 510 18" aria-hidden="true">
    <polygon points="0,0 348,0 331,18 0,18" fill="var(--orange)"/>
    <polygon points="379,0 510,0 510,18 362,18" fill="var(--purple)"/>
  </svg>
</section>

<section class="card card--jonas" aria-label="Rückseite Jonas Prasken">
  <div class="brand brand--small"><span class="brand__dot"></span>Vitalis Partner</div>
  <h2 class="person">Jonas Prasken <span class="person__role">(CoS)</span></h2>
  <div class="direct">
    <div class="line"><svg class="icon" viewBox="0 0 13 12"><rect x="3" y="1" width="6" height="10" rx="1" fill="none" stroke="var(--purple)" stroke-width="1.3"/><path d="M10 3.5q1.5 2.5 0 5" fill="none" stroke="var(--purple)"/></svg>+49 152 38 61 74 20</div>
    <div class="line"><svg class="icon" viewBox="0 0 13 12"><rect x="0.5" y="2.5" width="12" height="8" fill="none" stroke="var(--purple)"/><path d="M0.5 2.5l6 5 6-5" fill="none" stroke="var(--purple)"/></svg>jonas.prasken@vitalis-partner.de</div>
  </div>
  <div class="rule"></div>
  <div class="company">
    <div class="company__name">Vitalis Partner GmbH</div>
    <div>Lindenhof 12<span class="sep">·</span>D-26210 Grünstedt</div>
    <div class="line"><svg class="icon" viewBox="0 0 13 12"><path d="M1 5q5.5-5 11 0l-2 1.5-1.5-2h-4L3 6.5z" fill="var(--ink)"/><rect x="3" y="6.5" width="7" height="4" rx="1" fill="var(--ink)"/></svg>0800 5104 228<span class="sep">·</span><svg class="icon" viewBox="0 0 13 12"><rect x="0.5" y="2.5" width="12" height="8" fill="none" stroke="var(--purple)"/><path d="M0.5 2.5l6 5 6-5" fill="none" stroke="var(--purple)"/></svg>info@vitalis-partner.de</div>
    <div class="line"><svg class="icon" viewBox="0 0 13 12"><circle cx="6.5" cy="6" r="5.3" fill="none" stroke="var(--ink)"/><path d="M4 3l3 1-1 3 2 2" fill="none" stroke="var(--ink)" stroke-width="1.4"/></svg>www.vitalis-partner.de</div>
  </div>
  <svg class="band" viewBox="0 0 510 18" aria-hidden="true">
    <polygon points="0,0 348,0 331,18 0,18" fill="var(--orange)"/>
    <polygon points="379,0 510,0 510,18 362,18" fill="var(--purple)"/>
  </svg>
</section>

</body>
</html>
```